Brivolt Technologies business card design

We need a business card designed with our new logo. it would be great if the card could communicate it is a technology based company.

Target Market(s)

system integrators

Industry/Entity Type

technology, IOT

Contact Information for Business Card

Name, designation, Address, telephone number, email address

Requirements
Must have
• logo and company name
Nice to have
• something to do with technology

```html
<!DOCTYPE html>
<html lang="en">
<head>
<meta charset="utf-8">
<title>Brivolt Technologies – Business Card</title>
<link href="https://fonts.googleapis.com/css2?family=Open+Sans:ital,wght@0,400;0,700;1,400&display=swap" rel="stylesheet">
<style>
  :root {
    --page: #2a2a2a;
    --card: #1b1b1b;
    --accent: #f7941d;
    --text: #ffffff;
    --muted: #d9d9d9;
    --deco-light: #5a5a5a;
    --deco-dark: #1e1e1e;
  }
  * { margin: 0; padding: 0; box-sizing: border-box; }
  html, body {
    width: 1200px; height: 900px; overflow: hidden;
    background: var(--page);
    font-family: "Open Sans", Arial, sans-serif;
  }
  .card {
    position: absolute; left: 280px;
    width: 640px; height: 366px;
    background: var(--card);
    border: 1px solid var(--accent);
    box-shadow: 0 10px 30px rgba(0,0,0,.45);
    color: var(--text);
    overflow: hidden;
  }
  .card--front { top: 60px; }
  .card--back  { top: 474px; }

  .wordmark { display: flex; align-items: center; gap: 12px; }
  .wordmark__mark { width: 18px; height: 18px; background: var(--accent); flex: none; }
  .wordmark__name {
    font-weight: 700; color: var(--text);
    letter-spacing: 1px; text-transform: uppercase; line-height: 1;
  }

  .card--front .wordmark { position: absolute; left: 150px; top: 44px; }
  .card--front .wordmark__name { font-size: 30px; }

  .front-emblem {
    position: absolute; right: 40px; top: 110px;
    width: 210px; height: 150px;
    background: linear-gradient(135deg, #232323, #1d1d1d);
  }

  .person { position: absolute; left: 60px; top: 118px; }
  .person__name {
    color: var(--accent); font-weight: 700; font-size: 22px;
    text-transform: uppercase; letter-spacing: .3px;
  }
  .person__role { font-style: italic; font-size: 15px; color: var(--muted); margin-top: 2px; }

  .contacts { position: absolute; left: 60px; top: 188px; list-style: none; }
  .contacts li {
    display: flex; align-items: center; gap: 10px;
    font-size: 15px; line-height: 26px; color: var(--text);
  }
  .contacts svg { width: 13px; height: 13px; fill: var(--accent); flex: none; }

  .address {
    position: absolute; right: 48px; bottom: 30px;
    text-align: right; font-size: 15px; line-height: 23px;
    color: var(--text); font-style: normal;
  }

  .back-emblem {
    position: absolute; left: 0; top: 0;
    width: 640px; height: 250px;
    background: linear-gradient(160deg, var(--deco-dark) 0%, var(--deco-light) 55%, var(--deco-dark) 100%);
    opacity: .55;
  }
  .card--back .wordmark {
    position: absolute; right: 48px; bottom: 44px;
  }
  .card--back .wordmark__name { font-size: 34px; }
</style>
</head>
<body>

<section class="card card--front" aria-label="Business card front">
  <div class="wordmark">
    <span class="wordmark__mark"></span>
    <span class="wordmark__name">Brivolt Technologies</span>
  </div>

  <div class="front-emblem" role="img" aria-label="Faint company emblem decoration"></div>

  <div class="person">
    <div class="person__name">Daren Kolwick</div>
    <div class="person__role">President</div>
  </div>

  <ul class="contacts">
    <li>
      <svg viewBox="0 0 24 24" aria-hidden="true"><path d="M6.6 10.8a15.1 15.1 0 0 0 6.6 6.6l2.2-2.2c.3-.3.7-.4 1-.2 1.1.4 2.3.6 3.6.6.6 0 1 .4 1 1V20c0 .6-.4 1-1 1A17 17 0 0 1 3 4c0-.6.4-1 1-1h3.5c.6 0 1 .4 1 1 0 1.3.2 2.5.6 3.6.1.3 0 .7-.2 1z"/></svg>
      555-014-2287
    </li>
    <li>
      <svg viewBox="0 0 24 24" aria-hidden="true"><path d="M2 5h20v14H2z M2 5l10 8 10-8"/></svg>
      info@brivolttechnologies.com
    </li>
    <li>
      <svg viewBox="0 0 24 24" aria-hidden="true"><circle cx="12" cy="12" r="10"/></svg>
      www.brivolttechnologies.com
    </li>
  </ul>

  <address class="address">
    4718 Lantern Bay Rd<br>
    Marisol CA 92701
  </address>
</section>

<section class="card card--back" aria-label="Business card back">
  <div class="back-emblem" role="img" aria-label="Large glossy company emblem decoration"></div>
  <div class="wordmark">
    <span class="wordmark__mark"></span>
    <span class="wordmark__name">Brivolt Technologies</span>
  </div>
</section>

</body>
</html>
```